Beautiful design for wordpress

I need a beautiful, colourful and feminine website. My business is called 'The Velvet Lantern', and I sell crystals, books, CD's, pendulums and other metaphysical items. I also provide Reiki (energy healing).
I want this design to be eye catching and inspire happiness and joy in those who see it. And I would love to see the use of the logo and its colours :)
Please add these on the web design: Home, About, Online store, Blog

Industry/Entity Type

Business

Requirements
Must have
• Colourful and playful, must use the logo somewhere, have the words on a menu saying 'Home, Blog, Online store and about' (or similar to those)And the design must stand out!
Should not have
• grey, brown and other boring colours.

```html
<!DOCTYPE html>
<html lang="en">
<head>
<meta charset="utf-8">
<title>The Velvet Lantern</title>
<link href="https://fonts.googleapis.com/css2?family=Open+Sans:wght@300;400;600;700&display=swap" rel="stylesheet">
<style>
:root{
  --orange:#f7941d;
  --orange-dark:#f08a12;
  --text:#444;
  --muted:#888;
  --line:#e2e2e2;
  --dark:#333;
  --footer-top:#3d3d3d;
  --footer-bottom:#2c2c2c;
  --bar:#242424;
  --white:#fff;
  --logo:#6b5a8c;
}
*{box-sizing:border-box;margin:0;padding:0}
html,body{width:720px;height:1200px;overflow:hidden;background:var(--white)}
body{font-family:'Open Sans',sans-serif;color:var(--text);position:relative}
.abs{position:absolute}
.top-line{left:0;top:0;width:720px;height:2px;background:var(--orange)}
.brand{left:56px;top:26px;display:flex;align-items:center;gap:6px}
.brand-dot{width:14px;height:14px;border-radius:50%;background:var(--orange)}
.brand-name{font-size:15px;font-weight:600;color:var(--logo)}
.search{left:432px;top:17px;width:188px;height:18px;border:1px solid #d5d5d5;font-size:7px;color:#999;padding:4px 6px}
.search-btn{left:596px;top:17px;width:24px;height:18px;background:var(--orange);display:flex;align-items:center;justify-content:center}
.currency{left:432px;top:38px;font-size:8px;color:#bbb;display:flex;gap:6px;align-items:center}
.currency .on{color:#e64a2e}
.flag{width:12px;height:8px;background:linear-gradient(#c33 0 25%,#fff 25% 50%,#c33 50% 75%,#fff 75%);position:relative}
.flag::before{content:"";position:absolute;left:0;top:0;width:5px;height:4px;background:#335}
.cart{left:626px;top:17px;width:34px;height:30px;border:1px solid #ddd;border-radius:2px;display:flex;align-items:center;justify-content:center}
.nav{top:73px;font-size:8.5px;color:#666;display:flex;left:353px;gap:0}
.nav a{position:absolute;white-space:nowrap;text-decoration:none;color:#666}
.nav a.active{color:var(--orange)}
.header-line{left:0;top:95px;width:720px;height:1px;background:#e8e8e8}
.hero{left:0;top:95px;width:720px;height:309px;background:linear-gradient(100deg,#e9ddd3 0%,#e3b999 35%,#f1d7c6 55%,#f6f2ee 100%)}
.hero-arrow{width:26px;height:26px;border-radius:50%;display:flex;align-items:center;justify-content:center}
.hero-arrow.left{left:30px;top:235px;background:var(--white)}
.hero-arrow.right{left:661px;top:235px;background:rgba(247,148,29,.55)}
.hero-card{left:479px;top:174px;width:159px;height:163px;background:rgba(255,255,255,.95);text-align:center;padding:18px 10px 0}
.hero-card h1{font-size:13px;font-weight:600;letter-spacing:.5px;color:#333}
.hero-card p{font-size:7.6px;line-height:10.2px;color:#555;margin-top:11px}
.btn{display:inline-block;font-size:7px;font-weight:700;color:var(--white);text-align:center;letter-spacing:.4px}
.hero-card .btn{position:absolute;left:46px;top:128px;width:72px;height:16px;line-height:16px;background:var(--orange)}
.section-title{font-size:11px;font-weight:600;color:#333;text-align:center;width:720px;left:0}
.mini-arrow{width:11px;height:11px;border-radius:50%;top:445px}
.sell-box{left:62px;top:480px;width:598px;height:205px;border:1px solid var(--line)}
.sell-col{top:0;height:203px;text-align:center}
.sell-col+.sell-col{border-left:1px solid var(--line)}
.sell-img{position:absolute;top:5px;height:80px}
.sell-col h2{position:absolute;left:0;right:0;top:101px;font-size:9.5px;font-weight:600;color:#444}
.sell-col h2.hot{color:var(--orange)}
.sell-col p{position:absolute;left:12px;right:12px;top:118px;font-size:6.8px;line-height:10px;color:#777}
.sell-col .btn{position:absolute;top:162px;width:36px;height:17px;line-height:17px;border-radius:2px;background:#3a3a3a}
.sell-col .btn.hot{background:var(--orange)}
.product{top:774px;height:101px;width:132px}
.product.featured{background:linear-gradient(#f7a43a,#f68b1f);text-align:center;color:var(--white)}
.product.featured::after{content:"";position:absolute;right:0;top:0;border-style:solid;border-width:0 10px 10px 0;border-color:transparent #fff transparent transparent}
.icon-round{display:inline-flex;width:25px;height:25px;border-radius:50%;background:#3a3a3a;align-items:center;justify-content:center;margin:25px 2px 0}
.product .label{font-size:8px;margin-top:7px}
.product .price{font-size:7.5px}
.side-arrow{top:814px;width:20px;height:21px;display:flex;align-items:center;justify-content:center}
.footer{left:0;top:938px;width:720px;height:230px;background:linear-gradient(var(--footer-top),var(--footer-bottom))}
.f-col{top:32px}
.f-col h3{font-size:22px;font-weight:300;color:#eee;white-space:nowrap}
.f-col ul{list-style:none;margin-top:13px}
.f-col li{font-size:11px;font-weight:300;color:#ccc;height:21.8px;line-height:20px;padding-left:12px;position:relative;white-space:nowrap}
.f-col li::before{content:"";position:absolute;left:2px;top:9px;width:3px;height:3px;border:1px solid #ccc;border-radius:50%}
.f-col li.active{background:var(--orange);color:#fff;margin-left:-1px;width:135px}
.f-col li.active::before{border-color:#fff;background:#fff}
.field{left:522px;width:134px;background:#262626;border:1px solid #4a4a4a;border-radius:2px;font-size:6.5px;font-style:italic;color:#ddd;padding:4px 5px}
.send{left:590px;top:1114px;width:66px;height:17px;line-height:17px;background:var(--orange);border-radius:2px;color:#fff;font-size:8.5px;text-align:center}
.bar{left:0;top:1168px;width:720px;height:32px;background:var(--bar)}
.copy{left:64px;top:1181px;font-size:7px;color:#ddd}
.social{top:1180px;width:10px;height:10px;border-radius:50%;background:#888}
</style>
</head>
<body>
<div class="abs top-line"></div>

<header>
  <div class="abs brand"><span class="brand-dot"></span><span class="brand-name">The Velvet Lantern</span></div>
  <div class="abs search">Search item here</div>
  <div class="abs search-btn">
    <svg width="9" height="9" viewBox="0 0 10 10"><circle cx="4" cy="4" r="3" fill="none" stroke="#fff" stroke-width="1.5"/><line x1="6.2" y1="6.2" x2="9" y2="9" stroke="#fff" stroke-width="1.5"/></svg>
  </div>
  <div class="abs currency"><span class="on">$</span>|<span>€</span>|<span>£</span><span class="flag" style="margin-left:22px"></span></div>
  <div class="abs cart">
    <svg width="16" height="14" viewBox="0 0 16 14"><path d="M1 2h2.5l2 7h7l1.5-5H5" fill="none" stroke="#555" stroke-width="1.2"/><circle cx="6.5" cy="11.8" r="1.1" fill="#555"/><circle cx="11.5" cy="11.8" r="1.1" fill="#555"/></svg>
  </div>
  <nav class="abs nav">
    <a class="active" style="left:0">HOME</a>
    <a style="left:56px">ABOUT</a>
    <a style="left:115px">ONLINE STORE</a>
    <a style="left:205px">BLOG</a>
    <a style="left:259px">CONTACT US</a>
  </nav>
  <div class="abs header-line"></div>
</header>

<section>
  <div class="abs hero" role="img" aria-label="Woman relaxing with eyes closed receiving a Reiki energy healing treatment"></div>
  <div class="abs hero-arrow left"><svg width="10" height="10" viewBox="0 0 10 10"><path d="M6.5 1.5L3 5l3.5 3.5" fill="none" stroke="#555" stroke-width="1.6"/></svg></div>
  <div class="abs hero-arrow right"><svg width="10" height="10" viewBox="0 0 10 10"><path d="M3.5 1.5L7 5 3.5 8.5" fill="none" stroke="#fff" stroke-width="1.6"/></svg></div>
  <div class="abs hero-card">
    <h1>VELVET LANTERN</h1>
    <p>Northwood Panels is a leading manufacturer of custom interior hardwood shutters. We have always set the very highest standards of quality and craftsmanship for the shutters we</p>
    <span class="btn">READ MORE</span>
  </div>
</section>

<section>
  <div class="abs section-title" style="top:443px">WE SELL</div>
  <svg class="abs mini-arrow" style="left:284px" viewBox="0 0 11 11"><circle cx="5.5" cy="5.5" r="5.5" fill="#f9c48a"/><path d="M6.5 3L4 5.5 6.5 8" fill="none" stroke="#fff" stroke-width="1.3"/></svg>
  <svg class="abs mini-arrow" style="left:405px" viewBox="0 0 11 11"><circle cx="5.5" cy="5.5" r="5.5" fill="#ccc"/><path d="M4.5 3L7 5.5 4.5 8" fill="none" stroke="#fff" stroke-width="1.3"/></svg>

  <div class="abs sell-box">
    <div class="abs sell-col" style="left:0;width:140px">
      <div class="sell-img" style="left:5px;width:129px;background:linear-gradient(#1d2a4a,#6a7fb8 60%,#2b2f4a)" role="img" aria-label="Cluster of clear quartz crystals"></div>
      <h2 class="hot">CRYSTALS</h2>
      <p>Lorem ipsum dolor sit amet, consectetur adipiscing elit. Praesent vestibulum scelerisque</p>
      <span class="btn hot" style="left:52px">MORE</span>
    </div>
    <div class="abs sell-col" style="left:140px;width:153px">
      <div class="sell-img" style="left:7px;width:139px;background:linear-gradient(120deg,#5a4638,#e8e4df 55%,#8a7d72)" role="img" aria-label="Stack of books with cassettes and a CD"></div>
      <h2>BOOKS &amp; CD'S</h2>
      <p>Aliquam sit amet nibh luctus neque adipiscing mattis vel id nisi. Donec placerat magna interd</p>
      <span class="btn" style="left:58px">MORE</span>
    </div>
    <div class="abs sell-col" style="left:293px;width:153px">
      <div class="sell-img" style="left:7px;width:139px;background:radial-gradient(circle at 50% 35%,#f8efe6,#c9a78e 70%,#8f6e5b)" role="img" aria-label="Open hands holding a glowing light"></div>
      <h2>REIKI (ENERGY HEALING)</h2>
      <p>Quam fringilla, non fringilla dui vestibulum. Phasellus iaculis in turpis et accumsan</p>
      <span class="btn" style="left:58px">MORE</span>
    </div>
    <div class="abs sell-col" style="left:446px;width:151px">
      <div class="sell-img" style="left:7px;width:139px;background:linear-gradient(135deg,#f3efe6,#e0c98a 50%,#f4f0e8)" role="img" aria-label="Golden pendulum on a chain"></div>
      <h2>PENDULUMS</h2>
      <p>Duis ut facilisis nunc, congue luctus nibh. Curabitur pharetra nisl id la amet lorem ipsum</p>
      <span class="btn" style="left:58px">MORE</span>
    </div>
  </div>
</section>

<section>
  <div class="abs section-title" style="top:734px">OUR PRODUCTS</div>
  <div class="abs side-arrow" style="left:0;background:#bbb"><svg width="8" height="8" viewBox="0 0 8 8"><path d="M5 1L2 4l3 3" fill="none" stroke="#fff" stroke-width="1.3"/></svg></div>
  <div class="abs side-arrow" style="left:700px;background:#f9c48a"><svg width="8" height="8" viewBox="0 0 8 8"><path d="M3 1l3 3-3 3" fill="none" stroke="#fff" stroke-width="1.3"/></svg></div>

  <div class="abs product" style="left:60px;background:linear-gradient(135deg,#f4f4f4,#dcdcdc)" role="img" aria-label="Silver pendulum with rose quartz stone"></div>
  <div class="abs product featured" style="left:215px">
    <span class="icon-round"><svg width="12" height="12" viewBox="0 0 12 12"><rect x="1" y="4.5" width="6" height="3" rx="1.5" fill="none" stroke="#fff" stroke-width="1.3" transform="rotate(-45 4 6)"/><rect x="5" y="4.5" width="6" height="3" rx="1.5" fill="none" stroke="#fff" stroke-width="1.3" transform="rotate(-45 8 6)"/></svg></span>
    <span class="icon-round"><svg width="12" height="12" viewBox="0 0 16 14"><path d="M1 2h2.5l2 7h7l1.5-5H5" fill="none" stroke="#fff" stroke-width="1.4"/><circle cx="6.5" cy="11.8" r="1.1" fill="#fff"/><circle cx="11.5" cy="11.8" r="1.1" fill="#fff"/></svg></span>
    <div class="label">crystals</div>
    <div class="price">$373.28</div>
  </div>
  <div class="abs product" style="left:373px;background:radial-gradient(circle at 50% 45%,#2f6fd8,#1a3f9a 45%,#e6e8ee 75%)" role="img" aria-label="Blue copper sulfate crystal cluster"></div>
  <div class="abs product" style="left:529px;background:linear-gradient(120deg,#f06c6c,#eb5b5b 40%,#c9bfae 70%,#6b6e73)" role="img" aria-label="Open books with CDs on a pink background"></div>
</section>

<footer>
  <div class="abs footer">
    <div class="abs f-col" style="left:64px"><h3>Accessories</h3>
      <ul><li class="active">Crystals</li><li>Reiki</li><li>Shoes and Dresses</li><li>Pendulams</li><li>Accessories</li><li>Trends and Brands</li></ul></div>
    <div class="abs f-col" style="left:216px"><h3>Brands</h3>
      <ul><li>Trends</li><li>Jewellery</li><li>Shoes and Dresses</li><li>Holiday Shop</li><li>Accessories</li><li>Trends and Brands</li></ul></div>
    <div class="abs f-col" style="left:368px"><h3>Help</h3>
      <ul><li>Bags and Wallets</li><li>Jewellery</li><li>Shoes and Dresses</li><li>Holiday Shop</li><li>Accessories</li><li>Trends and Brands</li></ul></div>
    <div class="abs f-col" style="left:521px"><h3>Contact Us</h3></div>
  </div>
  <div class="abs field" style="top:1010px;height:19px">Name</div>
  <div class="abs field" style="top:1037px;height:18px">E-mail</div>
  <div class="abs field" style="top:1064px;height:38px">Message</div>
  <div class="abs send">Send Message</div>

  <div class="abs bar"></div>
  <div class="abs copy">Copyrights © 2014 your site -&nbsp; All Rights Reserved.</div>
  <span class="abs social" style="left:577px"></span>
  <span class="abs social" style="left:604px"></span>
  <span class="abs social" style="left:629px"></span>
  <span class="abs social" style="left:652px"></span>
</footer>
</body>
</html>
```